Business Card Design Project - 2 sided

We need a business card design for a card having one business on each side (ie. two businesses on one card). Would like a design that incorporates logo, tagline and normal fields (name, position, address, phone).

Would also like an allowance for small font text along the bottom (text to be determined, but less than 50 characters).

NB. Attached logo for Harbor Quill has two variations - either can be used.

www.harborquill-example.com / www.velmaro-example.com

```html
<!DOCTYPE html>
<html lang="en">
<head>
<meta charset="utf-8">
<title>Harbor Quill / Velmaro business card</title>
<link href="https://fonts.googleapis.com/css2?family=PT+Sans:wght@400;700&display=swap" rel="stylesheet">
<style>
  :root {
    --page-bg: #e9e6e1;
    --card-bg: #ffffff;
    --green: #8dc63f;
    --green-dark: #6fa83a;
    --navy: #2b2a6e;
    --blue: #2a8ac4;
    --text: #3a3a3a;
    --rule: #8a8a8a;
  }
  * { box-sizing: border-box; margin: 0; padding: 0; }
  html, body { width: 1200px; height: 402px; overflow: hidden; }
  body {
    background: var(--page-bg);
    font-family: "PT Sans", Arial, sans-serif;
    position: relative;
  }
  .card {
    position: absolute;
    top: 58px;
    width: 512px;
    height: 294px;
    background: var(--card-bg);
    border-radius: 22px;
    overflow: hidden;
    box-shadow: 0 2px 6px rgba(0,0,0,.18);
  }
  .card--harbor { left: 62px; }
  .card--velmaro { left: 626px; }
  .card__header { position: absolute; left: 0; top: 0; width: 512px; height: 110px; }
  .card__person {
    position: absolute; right: 36px; top: 28px;
    color: #fff; font-size: 15px;
  }
  .card__person strong { font-size: 17px; font-weight: 700; }
  .brand {
    position: absolute; display: flex; align-items: center; gap: 10px;
  }
  .brand__dot { width: 22px; height: 22px; border-radius: 50%; }
  .brand__name { font-weight: 700; line-height: 1; }
  .card--harbor .brand { left: 36px; top: 138px; }
  .card--harbor .brand__dot { background: var(--green); }
  .card--harbor .brand__name { font-size: 27px; color: var(--navy); letter-spacing: 1px; }
  .card--velmaro .brand { left: 44px; top: 100px; }
  .card--velmaro .brand__dot { background: var(--green); width: 34px; height: 34px; }
  .card--velmaro .brand__name { font-size: 40px; color: var(--blue); }
  .tagline { position: absolute; color: var(--text); }
  .card--harbor .tagline { left: 38px; top: 166px; font-size: 11px; font-weight: 700; }
  .card--velmaro .tagline { left: 112px; top: 140px; font-size: 12.5px; letter-spacing: .6px; }
  .contacts {
    position: absolute; left: 36px; top: 200px;
    display: flex; font-size: 13px; color: var(--text); line-height: 17.4px;
  }
  .contacts__col { padding-right: 10px; }
  .contacts__col + .contacts__col { border-left: 1px solid var(--rule); padding-left: 10px; }
  .contacts__col--phones { width: 152px; }
  .contacts__col--address { width: 155px; }
  .contacts__col--extra { font-size: 11px; }
  .contacts__row { display: flex; align-items: center; gap: 4px; }
  .icon { width: 10px; height: 10px; flex: none; }
  .contacts__lines { padding-top: 34px; }
</style>
</head>
<body>

<section class="card card--harbor">
  <svg class="card__header" viewBox="0 0 512 110" aria-hidden="true">
    <path d="M0 0H512V66C430 86 330 70 240 52C160 36 80 36 0 52Z" fill="var(--green)"/>
    <path d="M0 62C80 44 160 48 240 62C330 78 430 92 512 78V84C430 100 330 90 240 76C160 62 80 64 0 76Z" fill="var(--navy)"/>
  </svg>
  <p class="card__person"><strong>Your Name</strong> / Title</p>
  <div class="brand">
    <span class="brand__dot"></span>
    <span class="brand__name">HARBOR QUILL</span>
  </div>
  <p class="tagline">Website Translation and Localisation Specialist...</p>
  <div class="contacts">
    <div class="contacts__col contacts__col--phones">
      <div class="contacts__row"><svg class="icon" viewBox="0 0 10 10"><circle cx="5" cy="5" r="5" fill="var(--green)"/><path d="M3 2.5l1.3 1.2-.6.8 1.8 1.8.8-.6 1.2 1.3-1 .9C4.5 7.6 2.4 5.5 2.1 3.5z" fill="#fff"/></svg>123-456-7890</div>
      <div class="contacts__row"><svg class="icon" viewBox="0 0 10 10"><rect x="2.5" y="0" width="5" height="10" rx="1" fill="var(--green)"/><rect x="3.5" y="1.5" width="3" height="5" fill="#fff"/></svg>123-456-7890</div>
      <div class="contacts__row"><svg class="icon" viewBox="0 0 10 10"><rect x="1" y="4" width="8" height="6" rx="1" fill="var(--green)"/><rect x="0" y="1" width="10" height="2.5" rx="1" fill="var(--green)"/></svg>123-456-7890</div>
      <div class="contacts__row"><svg class="icon" viewBox="0 0 10 10"><circle cx="5" cy="5" r="5" fill="var(--green)"/><path d="M2 3.5h6v3.5H2zM2 3.5l3 2 3-2" fill="none" stroke="#fff" stroke-width=".8"/></svg>name@website.com</div>
      <div class="contacts__row"><svg class="icon" viewBox="0 0 10 10"><circle cx="5" cy="5" r="5" fill="var(--green)"/><path d="M1 5h8M5 1v8" stroke="#fff" stroke-width=".7"/></svg>www.website.com</div>
    </div>
    <div class="contacts__col contacts__col--address contacts__lines">
      <p>Complex name, Street</p>
      <p>City, State, zip code</p>
    </div>
    <div class="contacts__col contacts__col--extra contacts__lines">
      <p>xxxxxxxxxxxxxxxxxxxx</p>
      <p>xxxxxxxxxxxxxxxxxxxx</p>
    </div>
  </div>
</section>

<section class="card card--velmaro">
  <svg class="card__header" viewBox="0 0 512 110" aria-hidden="true">
    <defs>
      <linearGradient id="velmaroGreen" x1="0" x2="1" y1="0" y2="0">
        <stop offset="0" stop-color="var(--green)"/>
        <stop offset="1" stop-color="var(--green-dark)"/>
      </linearGradient>
    </defs>
    <path d="M0 0H512V66C430 86 330 70 240 52C160 36 80 36 0 52Z" fill="url(#velmaroGreen)"/>
    <path d="M0 62C80 44 160 48 240 62C330 78 430 92 512 78V84C430 100 330 90 240 76C160 62 80 64 0 76Z" fill="var(--blue)"/>
  </svg>
  <p class="card__person"><strong>Your Name</strong> / Title</p>
  <div class="brand">
    <span class="brand__dot"></span>
    <span class="brand__name">Velmaro</span>
  </div>
  <p class="tagline">Professional SEO Services</p>
  <div class="contacts">
    <div class="contacts__col contacts__col--phones">
      <div class="contacts__row"><svg class="icon" viewBox="0 0 10 10"><circle cx="5" cy="5" r="5" fill="var(--green)"/><path d="M3 2.5l1.3 1.2-.6.8 1.8 1.8.8-.6 1.2 1.3-1 .9C4.5 7.6 2.4 5.5 2.1 3.5z" fill="#fff"/></svg>123-456-7890</div>
      <div class="contacts__row"><svg class="icon" viewBox="0 0 10 10"><rect x="2.5" y="0" width="5" height="10" rx="1" fill="var(--green)"/><rect x="3.5" y="1.5" width="3" height="5" fill="#fff"/></svg>123-456-7890</div>
      <div class="contacts__row"><svg class="icon" viewBox="0 0 10 10"><rect x="1" y="4" width="8" height="6" rx="1" fill="var(--green)"/><rect x="0" y="1" width="10" height="2.5" rx="1" fill="var(--green)"/></svg>123-456-7890</div>
      <div class="contacts__row"><svg class="icon" viewBox="0 0 10 10"><circle cx="5" cy="5" r="5" fill="var(--green)"/><path d="M2 3.5h6v3.5H2zM2 3.5l3 2 3-2" fill="none" stroke="#fff" stroke-width=".8"/></svg>name@website.com</div>
      <div class="contacts__row"><svg class="icon" viewBox="0 0 10 10"><circle cx="5" cy="5" r="5" fill="var(--green)"/><path d="M1 5h8M5 1v8" stroke="#fff" stroke-width=".7"/></svg>www.website.com</div>
    </div>
    <div class="contacts__col contacts__col--address contacts__lines">
      <p>Complex name, Street</p>
      <p>City, State, zip code</p>
    </div>
    <div class="contacts__col contacts__col--extra contacts__lines">
      <p>xxxxxxxxxxxxxxxxxxxx</p>
      <p>xxxxxxxxxxxxxxxxxxxx</p>
    </div>
  </div>
</section>

</body>
</html>
```